Classy, Elegant, Simple Business Card Design

Looking to have a classy, simple, and elegant design. Want a top notch designed business card. I really like the look of the new torvane credit card. I also like the design I attached. I am trying to reach 21-29 year old females for booking us for there wedding or event. We offer Disc Jockey Service, Photo Booth Rentals, and Uplighting .

Target Market(s)

21-28 year old females

Contact Information for Business Card

Has to have logo, website, email, and phone number

Font styles to use
Other font styles liked:
• open to font choice, modern, clean
Designer to choose
33a6d7
0791cd
0555a3
ffffff

Requirements
Must have
• Has to have logo, website, email, and phone number
Nice to have
• I really like the design of the new torvane credit card. I also included my logo and some designs I like
Should not have
• clutter or too much info

```html
<!DOCTYPE html>
<html lang="en">
<head>
<meta charset="utf-8">
<title>Velmora – Business Card</title>
<link rel="stylesheet" href="https://fonts.googleapis.com/css2?family=Questrial&family=Roboto:wght@400;500&display=swap">
<style>
  :root {
    --page-bg: #d9d9d9;
    --card-bg: #f4f4f5;
    --navy: #0e2a55;
    --royal: #0555a3;
    --azure: #0791cd;
    --sky: #33a6d7;
    --mist: #c9dfec;
    --ink: #2b2f36;
  }
  * { box-sizing: border-box; margin: 0; padding: 0; }
  html, body { width: 1200px; height: 576px; overflow: hidden; }
  body { background: var(--page-bg); position: relative; font-family: "Roboto", Arial, sans-serif; }

  .card {
    position: absolute;
    background: var(--card-bg);
    border-radius: 10px;
    overflow: hidden;
  }
  .card--front { left: 82px; top: 139px; width: 484px; height: 295px; }
  .card--back  { left: 602px; top: 138px; width: 481px; height: 292px; }

  .brand-name {
    font-family: "Questrial", Arial, sans-serif;
    color: var(--navy);
    font-weight: 400;
    letter-spacing: 0.5px;
    display: flex;
    align-items: center;
    gap: 10px;
    white-space: nowrap;
  }
  .brand-dot { border-radius: 50%; background: var(--azure); flex: none; }

  .front-brand {
    position: absolute; left: 0; right: 0; top: 112px;
    justify-content: center; font-size: 36px;
  }
  .front-brand .brand-dot { width: 16px; height: 16px; }

  .front-band {
    position: absolute; left: 0; right: 0; bottom: 0; height: 40px;
    background: linear-gradient(to bottom, rgba(51,166,215,0.15), var(--azure) 55%, var(--royal));
  }

  .back-burst {
    position: absolute; left: -42px; top: 6px; width: 280px; height: 280px;
    border-radius: 50%;
    background: radial-gradient(circle, var(--card-bg) 0 60%, var(--mist) 62%, rgba(201,223,236,0.35) 85%, rgba(201,223,236,0) 100%);
  }
  .back-burst-name {
    position: absolute; left: 16px; top: 130px; width: 164px;
    justify-content: center; font-size: 28px; color: var(--azure);
  }

  .back-details { position: absolute; left: 284px; top: 56px; }
  .back-brand { font-size: 24px; }
  .back-brand .brand-dot { width: 10px; height: 10px; }

  .person-name { margin-top: 38px; font-size: 21px; font-weight: 500; color: var(--royal); }
  .person-role { margin-top: 3px; font-size: 12px; color: var(--ink); }

  .contact-list { list-style: none; margin-top: 22px; }
  .contact-item {
    display: flex; align-items: center; gap: 10px;
    font-size: 12.5px; color: var(--ink); height: 18.5px;
  }
  .contact-icon { width: 12px; height: 12px; flex: none; fill: var(--royal); }
</style>
</head>
<body>

<section class="card card--front" aria-label="Card front">
  <div class="brand-name front-brand"><span class="brand-dot"></span>VELMORA</div>
  <div class="front-band" role="img" aria-label="Decorative band of blue sound-level bars"></div>
</section>

<section class="card card--back" aria-label="Card back">
  <div class="back-burst" role="img" aria-label="Faint radial sound-burst decoration around the brand"></div>
  <div class="brand-name back-burst-name">Velmora</div>

  <div class="back-details">
    <div class="brand-name back-brand"><span class="brand-dot"></span>VELMORA</div>
    <p class="person-name">Mara Ellison</p>
    <p class="person-role">Founder &amp; CEO</p>
    <ul class="contact-list">
      <li class="contact-item">
        <svg class="contact-icon" viewBox="0 0 12 12" aria-hidden="true"><path d="M1 4c0-2 2-3 5-3s5 1 5 3v1H8.5V3.8h-5V5H1zM2.5 6h7l1 5h-9z"/></svg>
        555 0142 0188
      </li>
      <li class="contact-item">
        <svg class="contact-icon" viewBox="0 0 12 12" aria-hidden="true"><path d="M0 2h12v1L6 7 0 3zM0 4.2l6 4 6-4V10H0z"/></svg>
        mara@velmora.com
      </li>
      <li class="contact-item">
        <svg class="contact-icon" viewBox="0 0 12 12" aria-hidden="true"><circle cx="6" cy="6" r="5.2" fill="none" stroke="#0555a3" stroke-width="1.2"/><path d="M1 6h10M6 1c-3 3-3 7 0 10M6 1c3 3 3 7 0 10" fill="none" stroke="#0555a3" stroke-width="1"/></svg>
        www.velmora.com
      </li>
    </ul>
  </div>
</section>

</body>
</html>
```